Design a compelling Tarnwove Business Card that will drive people to my site

I want a business card that I can give to people—less to tell them who I am and more to direct them to my website. My website is a portal for Pelmor Aquatics Officials and a place for people who want to become Pelmor Aquatics Officials.
I am uploading my official company logo as well as a business card mockup that I did on my own. Please feel free to completely stray from this design.
I've included a screen recording of the homepage of my website as well.
Target Market(s)
Pelmor Aquatics Officials and people who desire to become one
Contact Information for Business Card
website url
Look and feel
Each slider illustrates characteristics of the customer's brand and the style your logo design should communicate.

```html
<!DOCTYPE html>
<html lang="en">
<head>
<meta charset="utf-8">
<title>Tarnwove Business Card</title>
<link rel="stylesheet" href="https://fonts.googleapis.com/css2?family=Poppins:wght@400;500;600;700&display=swap">
<style>
  :root {
    --stage: #1d1e21;
    --brand-blue: #2d4485;
    --card-grey: #d2d2d4;
    --ink-light: #dadade;
    --title-grey: #8a93b4;
  }
  * { margin: 0; padding: 0; box-sizing: border-box; }
  html, body { width: 1200px; height: 800px; overflow: hidden; }
  body {
    background: var(--stage);
    font-family: "Poppins", sans-serif;
    display: flex;
    align-items: center;
    justify-content: center;
    gap: 50px;
  }
  .card {
    position: relative;
    width: 525px;
    height: 300px;
    border-radius: 28px;
    overflow: hidden;
  }
  .card-contact { background: var(--card-grey); }
  .card-contact .wave { position: absolute; inset: 0; }
  .contact-logo {
    position: absolute;
    left: 42px;
    top: 112px;
    display: flex;
    align-items: center;
    gap: 10px;
    color: var(--ink-light);
    font-size: 32px;
    font-weight: 600;
    letter-spacing: -0.5px;
  }
  .logo-dot {
    width: 14px; height: 14px;
    border-radius: 50%;
    background: var(--ink-light);
  }
  .contact-details {
    position: absolute;
    left: 272px;
    top: 118px;
    color: var(--brand-blue);
  }
  .person-name { font-size: 22px; font-weight: 700; line-height: 1.1; }
  .person-title { font-size: 14px; font-weight: 400; color: var(--title-grey); margin-top: 2px; }
  .detail-rule { width: 36px; height: 2px; background: var(--brand-blue); margin: 12px 0 10px; }
  .detail-line { font-size: 14px; font-weight: 500; line-height: 1.45; }

  .card-site {
    background: var(--brand-blue);
    color: var(--ink-light);
    display: flex;
    flex-direction: column;
    justify-content: center;
    padding-left: 56px;
  }
  .site-brand { display: flex; align-items: center; gap: 12px; }
  .site-url { font-size: 58px; font-weight: 600; letter-spacing: -1px; line-height: 1; }
  .site-rule { width: 130px; height: 2px; background: var(--ink-light); margin: 18px 0 14px; }
  .site-tagline { font-size: 22px; font-weight: 400; letter-spacing: 0.5px; }
</style>
</head>
<body>
  <section class="card card-contact">
    <svg class="wave" viewBox="0 0 525 300" width="525" height="300" aria-hidden="true">
      <path d="M0,0 H350 C310,95 215,110 180,175 C155,225 150,270 140,300 H0 Z" fill="var(--brand-blue)"/>
    </svg>
    <div class="contact-logo"><span>tarnwove</span><span class="logo-dot"></span></div>
    <div class="contact-details">
      <p class="person-name">Martin Holloway</p>
      <p class="person-title">CEO &amp; Founder</p>
      <div class="detail-rule"></div>
      <p class="detail-line">martin@tarnwove.com</p>
      <p class="detail-line">(555) 014 - 2760</p>
    </div>
  </section>

  <section class="card card-site">
    <div class="site-brand"><span class="site-url">tarnwove.com</span></div>
    <div class="site-rule"></div>
    <p class="site-tagline">The unoffical Official Portal</p>
  </section>
</body>
</html>
```